Women's Health - Hormone Imbalance, Menopause, Perimenopause.

We need a poster to match a letter that will be sent out. So people see the poster in store they are reminded about the letter and the newspaper ad.
The Poster is advertising a holistic approach to treating menopause, perimenopause and women's health in general specifically hormonal imbalance.
This it the writing required on the poster
"Are you feeling out of sorts? Is your body changing? Could it be your hormones?
If you’re experiencing changes due to hormonal imbalances, it’s important to consult with a qualified medical professional who understands your needs.
Tarik Osmani, the vBlendwise Apothecary, can help. He has practiced pharmacy and nutritional medicine, helping people with hormone imbalances using a holistic approach for over 18 years.
Together, we look at issues around Hormonal Imbalance, Perimenopause and Menopause. To start, we take a profile of your sex hormones, Adrenals, Thyroids and Metabolic Pathways to see how we can best remedy the situation. Tarik uses a holistic approach that treats you as a whole – not just the symptoms – for overall better wellness.
Want to know more? Tarik is available for consultation on Wednesday Mornings at Larch Ridge Pharmacy and Thursday Mornings at Cove Brook Pharmacy.
SPECIAL OFFER! Make a booking for one session ($60) and get another session free! This limited-time package includes an initial consultation, historical hormone profile, follow-up consultation and wellness action plan.
To book an appointment with Tarik, call 1300 482 576 today."
Pictures required to correspond with the writing. I've also uploaded my logo
Industry/Entity Type
Pharmacy
Requirements
Must have
- Photos/Images to match the writing. Need women who are suffering from menopause with symptoms such as hot flashes, night sweats, anxiety, depression, fatigue, loss of libido, insomnia.
Nice to have
- Integrative Medicine, tailored medicine approach, Natural, approach, unique, tailor made solution

```html
<!DOCTYPE html>
<html lang="en">
<head>
<meta charset="utf-8">
<title>Are you feeling out of sorts? – Women's Hormone Health Poster</title>
<link rel="stylesheet" href="https://fonts.googleapis.com/css2?family=Alfa+Slab+One&family=Open+Sans:wght@300;400;600;700&family=PT+Sans+Narrow:wght@400;700&display=swap">
<style>
  :root {
    --orange: #e8961e;
    --slate: #3b3f4a;
    --slate-card: #4a4d53;
    --red: #a8222a;
    --red-offer: #a41f25;
    --yellow: #f3dc1c;
    --yellow-band: #e6e62c;
    --lime-text: #d6e23a;
    --navy: #0d4a6b;
    --navy-text: #1b2f6b;
    --ink: #111111;
    --white: #ffffff;
    --paper: #fbfbfb;
    --bg: #e9e9ea;
  }
  * { box-sizing: border-box; margin: 0; padding: 0; }
  html, body { width: 1200px; height: 1200px; overflow: hidden; background: var(--bg); }
  body { font-family: "Open Sans", Arial, sans-serif; position: relative; }

  .poster {
    position: absolute;
    left: 193px; top: 31px;
    width: 712px; height: 998px;
    background: var(--paper);
    transform: scale(1.14);
    transform-origin: top left;
    box-shadow: 0 6px 24px rgba(0,0,0,.18);
    overflow: hidden;
  }
  .abs { position: absolute; }

  /* Headline bubble */
  .headline { left: 29px; top: 30px; width: 659px; height: 100px; z-index: 3; }
  .headline svg { position: absolute; left: 0; top: 0; overflow: visible; }
  .headline h1 {
    position: absolute; left: 0; top: 12px; width: 659px; text-align: center;
    font-family: "Alfa Slab One", Georgia, serif; font-weight: 400;
    color: var(--white); font-size: 37px; letter-spacing: -.3px; white-space: nowrap;
  }

  /* Intro panel */
  .intro { left: 26px; top: 104px; width: 329px; height: 305px; background: var(--slate); }
  .pill {
    position: absolute; left: 7px; width: 320px; height: 46px;
    background: var(--red); border-radius: 23px;
    color: var(--white); font-weight: 300; font-size: 24px;
    display: flex; align-items: center; justify-content: center; white-space: nowrap;
    letter-spacing: -.4px;
  }
  .pill strong { color: var(--yellow); font-weight: 600; margin-left: 6px; }
  .pill .q { font-weight: 600; margin-left: 6px; }
  .pill-body { top: 15px; }
  .pill-hormones { top: 73px; }
  .intro-copy {
    position: absolute; left: 0; top: 136px; width: 329px; text-align: center;
    color: var(--white); font-weight: 300; font-size: 18.5px; line-height: 29px; letter-spacing: -.3px;
  }
  .intro-copy b { font-weight: 600; }
  .intro-copy .hl { color: var(--yellow); font-weight: 600; font-size: 25px; display: block; line-height: 30px; }

  .photo { display: block; }
  .hero-photo { left: 355px; top: 104px; width: 331px; height: 305px;
    background: linear-gradient(120deg, #eef0f2 0%, #d9c6b8 45%, #8a5a3c 75%, #eceae8 100%); }

  /* Bio banner */
  .bio-rule { left: 0; top: 440px; width: 712px; height: 2px; background: #5a5f66; }
  .bio { left: 36px; top: 409px; width: 640px; height: 50px; background: var(--navy);
    color: var(--white); font-family: "PT Sans Narrow", Arial, sans-serif; font-size: 14px;
    line-height: 21px; text-align: center; padding-top: 5px; }
  .bio b { font-weight: 700; }
  .bio-tab { top: 440px; }

  .together { left: 41px; top: 472px; color: var(--navy-text); font-weight: 600; font-size: 13px; }

  /* Issue cards */
  .issue { top: 500px; width: 208px; height: 211px; }
  .issue-title { height: 43px; background: var(--slate-card); border-top: 2px solid var(--red);
    color: var(--white); font-size: 15.5px; font-weight: 400; letter-spacing: .6px; text-align: center; line-height: 40px; white-space: nowrap; }
  .issue-photo { height: 168px; }
  .issue-imbalance { left: 23px; }
  .issue-peri { left: 253px; }
  .issue-meno { left: 481px; }
  .issue-imbalance .issue-photo { background: linear-gradient(160deg, #d9c3a8 0%, #b48a63 50%, #efe8e2 100%); }
  .issue-peri .issue-photo { background: linear-gradient(170deg, #9aa3bb 0%, #b9bdd0 55%, #d6b79f 100%); }
  .issue-meno .issue-photo { background: linear-gradient(150deg, #eeeae6 0%, #c9a784 50%, #8e6b4c 100%); }

  .profile { left: 0; top: 711px; width: 712px; height: 48px; background: var(--yellow-band);
    color: var(--ink); font-size: 11.4px; line-height: 15px; text-align: center; padding-top: 9px; letter-spacing: -.3px; }
  .profile b { font-weight: 600; }

  /* Contact */
  .contact { left: 0; top: 759px; width: 376px; height: 130px; background: var(--slate);
    color: var(--white); text-align: center; }
  .contact h2 { font-weight: 400; font-size: 21px; margin-top: 6px; }
  .contact p { font-size: 14.5px; line-height: 25.5px; margin-top: 6px; }
  .contact .y { color: var(--yellow); font-weight: 700; }
  .contact b { font-weight: 700; }

  .brand { left: 0; top: 889px; width: 376px; height: 45px; background: var(--white);
    border: 2px solid var(--slate); border-top: none;
    display: flex; align-items: center; justify-content: center; gap: 10px; }
  .brand-dot { width: 26px; height: 26px; border-radius: 50%; background: var(--navy-text); flex-shrink: 0; }
  .brand-name { font-weight: 700; font-size: 21px; color: var(--navy-text); letter-spacing: -.3px; white-space: nowrap; }

  .offer { left: 380px; top: 759px; width: 332px; height: 175px; background: var(--red-offer);
    color: var(--white); text-align: center; }
  .offer h2 { font-weight: 700; font-size: 22px; margin-top: 6px; }
  .offer .deal { color: var(--lime-text); font-weight: 700; font-size: 14px; line-height: 18px; margin-top: 3px; }
  .offer p { font-size: 14.5px; line-height: 18px; margin-top: 17px; padding: 0 14px; }

  .call { left: 0; top: 934px; width: 712px; height: 42px; }
  .call-bg { position: absolute; left: 0; top: 0; }
  .call-text { position: absolute; left: 24px; top: 8px; color: var(--white); font-weight: 600; font-size: 19px; white-space: nowrap; }
  .phone-icon { position: absolute; left: 480px; top: 8px; width: 26px; height: 26px; }
  .call-number { position: absolute; left: 511px; top: 2px; white-space: nowrap;
    color: var(--white); font-family: "PT Sans Narrow", Arial, sans-serif; font-weight: 700; font-size: 31px; line-height: 38px; }
</style>
</head>
<body>
<main class="poster">

  <header class="abs headline">
    <svg viewBox="0 0 659 100" width="659" height="100" aria-hidden="true">
      <path d="M37 0 H622 A37 37 0 0 1 622 74 H548 L522 94 L520 74 H37 A37 37 0 0 1 37 0 Z" fill="var(--orange)"/>
    </svg>
    <h1>Are you feeling out of sorts?</h1>
  </header>

  <section class="abs intro">
    <div class="pill pill-body">Is your <strong>body</strong><span class="q">changing ?</span></div>
    <div class="pill pill-hormones">Could it be your <strong>hormones ?</strong></div>
    <p class="intro-copy">
      If you’re experiencing <b>changes</b> due to
      <span class="hl">hormonal imbalances,</span>
      it’s important to consult with a<br>
      <b>qualified medical professional<br>who understands your needs.</b>
    </p>
  </section>

  <div class="abs photo hero-photo" role="img" aria-label="Photo of a young woman holding her head, looking tired and unwell"></div>

  <div class="abs bio-rule"></div>
  <svg class="abs bio-tab" style="left:16px" width="20" height="20" viewBox="0 0 20 20" aria-hidden="true"><path d="M20 0 V20 L0 1 Z" fill="var(--navy)"/></svg>
  <svg class="abs bio-tab" style="left:676px" width="20" height="20" viewBox="0 0 20 20" aria-hidden="true"><path d="M0 0 V20 L20 1 Z" fill="var(--navy)"/></svg>
  <div class="abs bio">
    <b>Tarik Osmani</b>, the <b>vBlendwise Apothecary</b>, can help. He has practiced <b>pharmacy</b> and <b>nutritional medicine</b>,<br>
    helping people with <b>hormone imbalances</b> using a <b>holistic approach</b> for <b>over 18 years</b>.
  </div>

  <p class="abs together">Together, we look at issues around</p>

  <article class="abs issue issue-imbalance">
    <h3 class="issue-title">HORMONAL IMBALANCE</h3>
    <div class="issue-photo" role="img" aria-label="Photo of a stressed woman with her hands in her hair"></div>
  </article>
  <article class="abs issue issue-peri">
    <h3 class="issue-title">PERIMENOPAUSE</h3>
    <div class="issue-photo" role="img" aria-label="Photo of a woman holding her abdomen in discomfort"></div>
  </article>
  <article class="abs issue issue-meno">
    <h3 class="issue-title">MENOPAUSE</h3>
    <div class="issue-photo" role="img" aria-label="Photo of a mature woman holding her temple with a headache"></div>
  </article>

  <p class="abs profile">
    To start, we take a profile of your <b>sex hormones</b>, <b>Adrenals</b>, <b>Thyroids</b> and <b>Metabolic Pathways</b> to see how we can best remedy<br>
    the situation. Tarik uses a holistic approach that treats you as a whole – not just the symptoms – for overall better wellness.
  </p>

  <section class="abs contact">
    <h2>Want to know more?</h2>
    <p>
      <span class="y">Tarik</span> is available for consultation on <span class="y">Wednesday</span><br>
      <span class="y">Mornings</span> at <b>Larch Ridge Pharmacy</b> and<br>
      <span class="y">Thursday Mornings</span> at <b>Cove Brook Pharmacy</b>.
    </p>
  </section>

  <div class="abs brand">
    <span class="brand-dot"></span>
    <span class="brand-name">vBlendwise Apothecary</span>
  </div>

  <section class="abs offer">
    <h2>SPECIAL OFFER</h2>
    <p class="deal">Make a booking for one session ($60) and<br>get another session free!</p>
    <p>This limited-time package includes an initial consultation, historical hormone profile, follow-up consultation and wellness action plan.</p>
  </section>

  <footer class="abs call">
    <svg class="call-bg" viewBox="0 0 712 42" width="712" height="42" aria-hidden="true">
      <rect width="712" height="42" fill="var(--ink)"/>
      <path d="M458 0 H712 V42 H480 Z" fill="var(--orange)"/>
    </svg>
    <span class="call-text">To book an appointment with Tarik, call today</span>
    <svg class="phone-icon" width="26" height="26" viewBox="0 0 28 28" aria-hidden="true">
      <circle cx="14" cy="14" r="12" fill="none" stroke="var(--red)" stroke-width="2"/>
      <path d="M9 8 l3 -1 l2 4 l-2 1.5 a8 8 0 0 0 3.5 3.5 l1.5 -2 l4 2 l-1 3 c-6 1 -12 -5 -11 -11 z" fill="var(--red)"/>
    </svg>
    <span class="call-number">1300 482 576</span>
  </footer>

</main>
</body>
</html>
```